Lanterns Across Still Water by Delia and Milo Ferris

Book Cover for a memoir - Lanterns Across Still Water and Other Small Mercies
Milo's pictures are below. He's the oldest of the three boys. Include angels, staircase, clouds, gift
light ocean blues and purples (maybe a little pink but not too feminine) and gold.
I imagine a pic of Milo walking up a staircase to Archangels or heaven but use your own creative imagination.
Here's a flavor for the book.
"My son is dead, and I speak with him every day.
Lanterns Across Still Water And Other Small Mercies is my memoir. It’s a story of love and loss, as I share my personal journey of losing my son at the same time as moving through a divorce, all of which turned out to be a gift that Milo gave me as he reached across the veil to hold my hand through the hardest season of my life, and helped me find love again after the breakdown of my marriage.
This is my personal story of how the gift Milo left me revealed the truth about what happens when we die.
Above all it is a story about the love shared between a mother and son, the unshakeable bond that even death cannot stand between. It shows us how our children can be our greatest teachers, just as death can be. And how losing ourselves can be the chance to find ourselves again, leading to hope and healing.
Milo and I wrote this book together to give the gift of our story to our readers. We share what we have walked through in hopes that we can help others who have lost a child learn how to communicate with them and heal in the best way possible, and to give comfort to those who are grieving the loss of other loved ones."

I added a few pictures. The two at the bottom of Milo walking away and turning to walk away would be good for a staircase.
And a few pics of design/colors I like

Parents who have lost children to death - anyone grieving a loved one

Serif
Decorative

0054AA
0677BA
7BADD7
CADEEF
E8F1F8
0094D4
00A9DD
6FCCEA
C7EBF8
E9F6FB
FFF300
FFF600
FEFA6F
FFFEC7
FFFEE8
A7469A
B969AE
D3A5CF
EDDBEB
F8F0F9
6B429C
8869AF
B7A5CE
E3DAEB
F3F0F8

• angel wings or angels on top, feel of heaven, Milo, simple (I have other pics that are better but can't upload). Any way I can add them somewhere? Like him walking away and better ones
• gifts/presents, soft colors, clouds, Milo walking into heaven
• not cartoony, not dark,

```html
<!DOCTYPE html>
<html lang="en">
<head>
<meta charset="utf-8">
<title>Lanterns Across Still Water — Book Cover Wrap</title>
<link rel="stylesheet" href="https://fonts.googleapis.com/css2?family=Kaushan+Script&family=Poppins:wght@300;400&family=Roboto:ital,wght@0,400;0,700;1,400&display=swap">
<style>
  :root {
    --stage: #2b2b2b;
    --sky-deep: #2d5a80;
    --sky-mid: #6f9fbf;
    --sky-cyan: #9edbe8;
    --sky-gold: #d8b58a;
    --sky-peach: #ecd3b4;
    --glow: #fffdf4;
    --ink-light: #ffffff;
    --figure-shirt: #f3f5f8;
    --figure-denim: #8fb2cf;
  }
  * { margin: 0; padding: 0; box-sizing: border-box; }
  html, body {
    width: 1200px; height: 1200px; overflow: hidden;
    background: var(--stage);
  }
  .cover-wrap {
    position: absolute; left: 40px; top: 197px;
    width: 1120px; height: 806px; overflow: hidden;
    color: var(--ink-light);
  }
  .sky-scene { position: absolute; inset: 0; width: 100%; height: 100%; }

  /* Back cover */
  .back-title {
    position: absolute; left: 78px; top: 82px; width: 380px;
    font-family: "Kaushan Script", cursive; font-size: 30px;
    text-align: center; white-space: nowrap;
  }
  .back-blurb {
    position: absolute; left: 78px; top: 139px; width: 376px;
    font-family: "Poppins", sans-serif; font-weight: 300;
    font-size: 10.3px; line-height: 13.7px; text-align: center;
  }
  .back-blurb p + p { margin-top: 13.7px; }
  .photo-collage {
    position: absolute; left: 85px; top: 458px; width: 360px; height: 205px;
    display: grid; gap: 1px; grid-template-rows: 80px 124px;
  }
  .collage-row { display: grid; gap: 1px; }
  .collage-row.top { grid-template-columns: 71px 59px 108px 1fr; }
  .collage-row.bottom { grid-template-columns: 168px 95px 1fr; }
  .collage-photo { width: 100%; height: 100%; }

  /* Spine */
  .spine-title, .spine-authors {
    position: absolute; left: 540px;
    writing-mode: vertical-rl; white-space: nowrap;
  }
  .spine-title {
    top: 48px; font-family: "Kaushan Script", cursive; font-size: 26px;
  }
  .spine-authors {
    top: 546px; left: 544px;
    font-family: "Roboto", sans-serif; font-size: 18px; font-weight: 700;
  }
  .spine-authors .by, .front-authors .by { font-weight: 400; font-style: italic; }

  /* Front cover */
  .front-title {
    position: absolute; left: 588px; top: 48px; width: 532px;
    font-family: "Kaushan Script", cursive; text-align: center; line-height: 1;
  }
  .front-title .line-small { display: block; font-size: 34px; }
  .front-title .line-mid { display: block; font-size: 64px; margin-top: -2px; }
  .front-title .line-big { display: block; font-size: 176px; margin-top: -14px; }
  .front-figure {
    position: absolute; left: 795px; top: 264px; width: 112px; height: 426px;
  }
  .front-eagle {
    position: absolute; left: 1050px; top: 598px; width: 168px; height: 70px;
  }
  .front-authors {
    position: absolute; left: 752px; top: 745px; width: 200px;
    font-family: "Roboto", sans-serif; font-size: 19px; font-weight: 700;
    text-align: center; white-space: nowrap;
  }
</style>
</head>
<body>
<main class="cover-wrap">
  <svg class="sky-scene" viewBox="0 0 1120 806" role="img" aria-label="Heavenly sky of blue and golden clouds with a glowing stairway rising through mist">
    <defs>
      <linearGradient id="skyBase" x1="0" y1="0" x2="1" y2="0.4">
        <stop offset="0" stop-color="var(--sky-deep)"/>
        <stop offset="0.35" stop-color="var(--sky-mid)"/>
        <stop offset="0.6" stop-color="var(--sky-gold)"/>
        <stop offset="1" stop-color="var(--sky-peach)"/>
      </linearGradient>
      <linearGradient id="mist" x1="0" y1="0" x2="0" y2="1">
        <stop offset="0.45" stop-color="var(--sky-cyan)" stop-opacity="0"/>
        <stop offset="1" stop-color="var(--sky-cyan)" stop-opacity="0.95"/>
      </linearGradient>
      <radialGradient id="glow" cx="0.76" cy="0.5" r="0.35">
        <stop offset="0" stop-color="var(--glow)" stop-opacity="0.95"/>
        <stop offset="1" stop-color="var(--glow)" stop-opacity="0"/>
      </radialGradient>
    </defs>
    <rect width="1120" height="806" fill="url(#skyBase)"/>
    <rect width="1120" height="806" fill="url(#glow)"/>
    <rect width="1120" height="806" fill="url(#mist)"/>
  </svg>

  <h2 class="back-title">Lanterns Across Still Water</h2>
  <div class="back-blurb">
    <p>Lorem ipsum dolor sit amet, consectetur adipiscing elit, sed do eiusmod tempor incididunt ut labore et dolore magna aliqua. Quis ipsum suspendisse ultrices gravida. Risus commodo viverra maecenas accumsan lacus vel facilisis. Lorem ipsum dolor sit amet, consectetur adipiscing elit, sed do eiusmod tempor incididunt ut labore et dolore magna aliqua. Quis ipsum suspendisse ultrices gravida. Risus commodo viverra maecenas accumsan lacus vel facilisis. Lorem ipsum dolor sit amet, consectetur adipiscing elit, sed do eiusmod tempor incididunt ut labore et dolore magna aliqua. Quis ipsum suspendisse ultrices gravida. Risus commodo viverra maecenas accumsan lacus vel facilisis.</p>
    <p>Lorem ipsum dolor sit amet, consectetur adipiscing elit, sed do eiusmod tempor incididunt ut labore et dolore magna aliqua. Quis ipsum suspendisse ultrices gravida. Risus commodo viverra maecenas accumsan lacus vel facilisis.Lorem ipsum dolor sit amet, consectetur adipiscing elit, sed do eiusmod tempor incididunt ut labore et dolore magna aliqua. Quis ipsum suspendisse ultrices gravida. Risus commodo viverra maecenas accumsan lacus vel facilisis. Lorem ipsum dolor sit amet, consectetur adipiscing elit, sed do eiusmod tempor incididunt ut labore et dolore magna aliqua. Quis ipsum suspendisse ultrices gravida. Risus commodo viverra maecenas accumsan lacus vel facilisis. Lorem ipsum dolor sit amet, consectetur adipiscing elit, sed do eiusmod tempor incididunt ut labore et dolore magna aliqua.</p>
  </div>

  <div class="photo-collage">
    <div class="collage-row top">
      <div class="collage-photo" role="img" aria-label="Family snapshot of Milo with loved ones" style="background:#6b5a55"></div>
      <div class="collage-photo" role="img" aria-label="Young Milo holding up a trophy" style="background:#3a3a42"></div>
      <div class="collage-photo" role="img" aria-label="Milo competing in a wrestling match" style="background:#2f3e55"></div>
      <div class="collage-photo" role="img" aria-label="Wrestling match in a crowded arena" style="background:#4a5a4e"></div>
    </div>
    <div class="collage-row bottom">
      <div class="collage-photo" role="img" aria-label="Milo with his little brother opening presents" style="background:#7a7470"></div>
      <div class="collage-photo" role="img" aria-label="Milo smiling and holding a certificate" style="background:#4e5660"></div>
      <div class="collage-photo" role="img" aria-label="Milo holding an award at night" style="background:#1e2028"></div>
    </div>
  </div>

  <div class="spine-title">Lanterns Across Still Water</div>
  <div class="spine-authors"><span class="by">by</span> Delia and Milo Ferris</div>

  <h1 class="front-title">
    <span class="line-small">Lanterns Across</span>
    <span class="line-mid">Still</span>
    <span class="line-big">Water</span>
  </h1>

  <svg class="front-figure" viewBox="0 0 112 426" role="img" aria-label="Milo in a white shirt and jeans turning back with a smile as he climbs the stairway">
    <defs>
      <linearGradient id="figureTone" x1="0" y1="0" x2="0" y2="1">
        <stop offset="0" stop-color="var(--figure-shirt)" stop-opacity="0.9"/>
        <stop offset="0.55" stop-color="var(--figure-shirt)" stop-opacity="0.85"/>
        <stop offset="0.7" stop-color="var(--figure-denim)" stop-opacity="0.8"/>
        <stop offset="1" stop-color="var(--figure-denim)" stop-opacity="0"/>
      </linearGradient>
    </defs>
    <rect x="10" y="0" width="92" height="426" rx="40" fill="url(#figureTone)"/>
  </svg>

  <svg class="front-eagle" viewBox="0 0 168 70" role="img" aria-label="Bald eagle soaring beside the stairway">
    <ellipse cx="84" cy="40" rx="80" ry="22" fill="#5b4e44" opacity="0.55"/>
  </svg>

  <div class="front-authors"><span class="by">by</span> Delia and Milo Ferris</div>
</main>
</body>
</html>
```